Simple and Clean business card design

We would like the design to be simple clean and to incorporate our colors.

We are open to your design and talent, we have the dots in our logo as we think of it as data points and we connect data points for people.

We are open to see the great creative and clean design you bring to the table

Contact Information for Business Card

please include: name, position, email, phone and website

Font styles to use
Sans Serif

Requirements
Must have
• my colors incorporated, simplicity
Nice to have
• lots of white space, simplicity
Should not have
• complexicity/ complex art

```html
<!DOCTYPE html>
<html lang="en">
<head>
<meta charset="utf-8">
<title>Quorvia business card</title>
<link href="https://fonts.googleapis.com/css2?family=Montserrat:wght@400;500;600&display=swap" rel="stylesheet">
<style>
  :root {
    --backdrop: #b1b1ac;
    --card: #1b1b1c;
    --edge: #5b80c6;
    --accent: #5b80c6;
    --ink: #ffffff;
    --ink-soft: #e6e6e6;
    --decor-glow: #2a2a2b;
  }
  * { box-sizing: border-box; margin: 0; padding: 0; }
  html, body { width: 1200px; height: 801px; overflow: hidden; }
  body {
    background: var(--backdrop);
    font-family: "Montserrat", sans-serif;
    position: relative;
  }
  .card {
    position: absolute;
    top: 252px;
    width: 520px;
    height: 297px;
    background: var(--card);
    border-bottom: 4px solid var(--edge);
    overflow: hidden;
    box-shadow: 0 14px 30px rgba(0,0,0,0.28);
  }
  .card--back { left: 45px; }
  .card--front { left: 635px; }

  .card__decor {
    position: absolute;
    left: 0; top: 0;
    width: 260px; height: 100%;
    background: radial-gradient(ellipse at 30% 45%, var(--decor-glow) 0%, var(--card) 70%);
  }

  .wordmark {
    position: absolute;
    display: flex;
    align-items: center;
    gap: 10px;
    color: var(--ink);
    font-weight: 600;
    letter-spacing: 0.5px;
    line-height: 1;
  }
  .wordmark__dot {
    border-radius: 50%;
    background: var(--accent);
    flex: none;
  }
  .card--back .wordmark { left: 30px; bottom: 62px; font-size: 42px; }
  .card--back .wordmark__dot { width: 14px; height: 14px; }
  .card--front .wordmark { right: 42px; top: 112px; font-size: 64px; }
  .card--front .wordmark__dot { width: 18px; height: 18px; }

  .divider {
    position: absolute;
    left: 262px; top: 58px;
    width: 1px; height: 180px;
    background: var(--accent);
  }
  .contact {
    position: absolute;
    left: 282px; top: 62px;
    color: var(--ink-soft);
    font-size: 12.5px;
    line-height: 1.45;
  }
  .contact__name {
    color: var(--accent);
    font-size: 19px;
    font-weight: 600;
    letter-spacing: 1.5px;
    text-transform: uppercase;
    line-height: 1.1;
  }
  .contact__role { margin-bottom: 12px; font-size: 13px; }
  .contact__address { margin-bottom: 12px; }
  .contact__row { display: flex; align-items: center; gap: 7px; }
  .contact__icon { width: 11px; height: 11px; flex: none; }
</style>
</head>
<body>

<section class="card card--back" aria-label="Card back with contact details">
  <div class="card__decor" role="img" aria-label="Soft decorative background of faint grey circles"></div>

  <div class="wordmark"><span class="wordmark__dot"></span>quorvia</div>

  <div class="divider"></div>

  <div class="contact">
    <p class="contact__name">Daniel Reyes</p>
    <p class="contact__role">Founder</p>
    <p class="contact__address">48 Orchard Lane<br>Fairview, TX 75069</p>
    <p class="contact__row">
      <svg class="contact__icon" viewBox="0 0 12 12" aria-hidden="true"><path d="M3 1 L5 3.5 L4 5 Q5 7 7 8 L8.5 7 L11 9 L9.5 11 Q5 11 1 5 Q1 2.5 3 1Z" fill="var(--ink-soft)"/></svg>
      0412 555 208
    </p>
    <p class="contact__row">
      <svg class="contact__icon" viewBox="0 0 12 12" aria-hidden="true"><rect x="1" y="2.5" width="10" height="7" fill="none" stroke="var(--ink-soft)" stroke-width="1"/><path d="M1 2.5 L6 6.5 L11 2.5" fill="none" stroke="var(--ink-soft)" stroke-width="1"/></svg>
      info@quorviadata.com
    </p>
    <p class="contact__row">
      <svg class="contact__icon" viewBox="0 0 12 12" aria-hidden="true"><circle cx="6" cy="6" r="5" fill="none" stroke="var(--ink-soft)" stroke-width="1"/><ellipse cx="6" cy="6" rx="2.2" ry="5" fill="none" stroke="var(--ink-soft)" stroke-width="0.8"/><path d="M1 6 H11" stroke="var(--ink-soft)" stroke-width="0.8"/></svg>
      www.quorviadata.com
    </p>
  </div>
</section>

<section class="card card--front" aria-label="Card front with company name">
  <div class="card__decor" role="img" aria-label="Soft decorative background of faint grey circles"></div>

  <div class="wordmark"><span class="wordmark__dot"></span>quorvia</div>
</section>

</body>
</html>
```